"Harbor Builders" is a residential building company and needs a new business card design and may re

We would like a redesign based on the existing logo, and would like to see a new font as well. We are bespoke home builders who build sustainable energy efficient homes.

Industry/Entity Type

Construction

Contact Information for Business Card

Business card size 40mm x 90mm

Colors

Designer to choose colors to be used in the design.

```html
<!DOCTYPE html>
<html lang="en">
<head>
<meta charset="utf-8">
<title>Harbor Builders – Business Card</title>
<link rel="stylesheet" href="https://fonts.googleapis.com/css2?family=Roboto:wght@400;500&family=Roboto+Condensed:wght@700&display=swap">
<style>
  :root {
    --backdrop: #5b4838;
    --card-white: #f2f2f2;
    --card-black: #070809;
    --lime: #b2c92b;
    --ink: #1a1a1a;
    --text-grey: #4a4a4a;
    --white: #f4f4f4;
  }
  * { margin: 0; padding: 0; box-sizing: border-box; }
  html, body { width: 1200px; height: 960px; overflow: hidden; }
  body {
    background: var(--backdrop);
    font-family: "Roboto", Arial, sans-serif;
    position: relative;
  }
  .card { position: absolute; width: 600px; height: 343px; }
  .card-front { left: 314px; top: 113px; background: var(--card-white); }
  .card-back { left: 311px; top: 472px; background: var(--card-black); }

  .name-band {
    position: absolute; left: 0; top: 43px; width: 330px; height: 78px;
    background: var(--card-black);
    clip-path: polygon(0 0, 100% 0, 86% 100%, 0 100%);
  }
  .person-name {
    position: absolute; left: 27px; top: 26px;
    font-family: "Roboto Condensed", "Arial Narrow", sans-serif;
    font-weight: 700; font-size: 22px; color: var(--lime);
  }
  .brand {
    position: absolute; left: 290px; top: 52px;
    display: flex; align-items: center; gap: 12px;
  }
  .brand-square { width: 26px; height: 26px; background: var(--lime); }
  .brand-name {
    font-weight: 500; font-size: 34px; line-height: 1; color: var(--ink);
  }

  .address {
    position: absolute; left: 40px; top: 188px;
    font-size: 15px; line-height: 19px; color: var(--text-grey);
  }
  .address .company { font-weight: 500; }
  .contacts {
    position: absolute; left: 40px; top: 254px;
    list-style: none; font-size: 15px; line-height: 19px; color: var(--text-grey);
  }
  .contacts li { display: flex; align-items: center; gap: 9px; }
  .contacts svg { width: 13px; height: 13px; flex: none; }
  .registration {
    position: absolute; right: 34px; top: 273px; text-align: right;
    font-size: 15px; line-height: 19px; color: var(--text-grey);
  }

  .back-brand {
    position: absolute; left: 0; right: 0; top: 130px;
    display: flex; justify-content: center; align-items: center; gap: 18px;
  }
  .back-brand .brand-square { width: 44px; height: 44px; }
  .back-brand .brand-name { font-size: 52px; color: var(--white); }
  .back-web {
    position: absolute; left: 0; right: 0; top: 298px; text-align: center;
    font-size: 14px; letter-spacing: 3px; color: var(--white);
  }
</style>
</head>
<body>
  <section class="card card-front">
    <div class="name-band">
      <span class="person-name">DANIEL MORELAND</span>
    </div>
    <div class="brand">
      <span class="brand-square"></span>
      <span class="brand-name">harbor builders</span>
    </div>

    <p class="address">
      <span class="company">Harbor Builders Pty Ltd</span><br>
      PO Box 4120 Eastgate<br>
      LPO Ridgeway WA 6099
    </p>

    <ul class="contacts">
      <li>
        <svg viewBox="0 0 13 13" aria-hidden="true"><rect x="3" y="0.5" width="7" height="12" rx="1.2" fill="none" stroke="#111" stroke-width="1.4"/><rect x="5.5" y="10" width="2" height="1" fill="#111"/></svg>
        0400 555 018
      </li>
      <li>
        <svg viewBox="0 0 13 13" aria-hidden="true"><rect x="1" y="3" width="11" height="7.5" fill="#111"/><path d="M1 3 L6.5 7.2 L12 3" fill="none" stroke="#f2f2f2" stroke-width="1"/></svg>
        daniel@harborbuilders.com.au
      </li>
      <li>
        <svg viewBox="0 0 13 13" aria-hidden="true"><circle cx="6.5" cy="6.5" r="5.8" fill="#111"/><path d="M4 3.5 Q6 4.5 5 6.5 Q7.5 7 8 10" fill="none" stroke="#f2f2f2" stroke-width="1.2"/></svg>
        www.harborbuilders.com.au
      </li>
    </ul>

    <p class="registration">
      Registration 10487<br>
      ABN: 12 345 678 901
    </p>
  </section>

  <section class="card card-back">
    <div class="back-brand">
      <span class="brand-square"></span>
      <span class="brand-name">harbor builders</span>
    </div>
    <p class="back-web">www.harborbuilders.com.au</p>
  </section>
</body>
</html>
```